Architectural, Engineering and Design Build

Tovandex4.com
Veteran Disabled Certified company is doing business in Architecture, Engineer and Design build - look simialr websites and come up with design follow following website
https://hollis-darnet.example/
https://www.venlorcogroup.example/
https://www.pembrisgc.example/contract-vehicles/service-disabled-veteran-owned-small-business-sdvosb/
https://www.corbelnetlink.example/about/sdvosb/

Target Market(s)

US - Defense and Federal Government

Industry/Entity Type

Colors
0054AA
0677BA
7BADD7
CADEEF
E8F1F8

Requirements
Must have
• Army, American patriotism , Buildings, construction, architecture, engineering
Nice to have
• I need to attract federal government agencies and Defense

```html
<!DOCTYPE html>
<html lang="en">
<head>
<meta charset="utf-8">
<title>Tovandex4 — Architecture, Engineering &amp; Design Build</title>
<link href="https://fonts.googleapis.com/css2?family=Exo+2:wght@600;700;800&family=Mulish:wght@400;600&family=Oswald:wght@400&display=swap" rel="stylesheet">
<style>
  :root{
    --navy:#0b1a5c;
    --navy-deep:#081347;
    --red:#db0a16;
    --red-soft:#e1262f;
    --white:#ffffff;
    --ink:#222222;
    --muted:#5a5a5a;
    --line:#e9e9e9;
  }
  *{box-sizing:border-box;margin:0;padding:0}
  html,body{width:1200px;height:3145px;overflow:hidden}
  body{position:relative;background:var(--white);font-family:"Mulish",sans-serif;color:var(--ink)}
  .backdrop{position:absolute;left:0;top:0;width:1200px;height:3145px}
  .abs{position:absolute}
  .heading{font-family:"Exo 2",sans-serif;font-weight:800;font-size:42px;letter-spacing:.5px;color:var(--navy)}
  .underline{position:absolute;width:22px;height:3px;background:var(--red)}
  .btn{position:absolute;display:flex;align-items:center;justify-content:center;width:139px;height:50px;border-radius:25px;background:var(--red);color:var(--white);font-family:"Exo 2",sans-serif;font-weight:700;font-size:14px;letter-spacing:.2px}

  /* header */
  .logo-disc{position:absolute;left:141px;top:0;width:156px;height:156px;border-radius:50%;background:var(--white);display:flex;align-items:center;justify-content:center;z-index:2}
  .brand-name{font-family:"Exo 2",sans-serif;font-weight:800;font-size:27px;color:var(--navy);letter-spacing:.5px}
  .call{position:absolute;right:145px;top:18px;display:flex;align-items:center;gap:8px;font-family:"Exo 2",sans-serif;font-weight:700;font-size:20px;color:var(--navy)}
  .call-icon{width:28px;height:28px;border-radius:50%;background:var(--red);display:flex;align-items:center;justify-content:center}
  .nav-bar{position:absolute;left:578px;top:62px;width:622px;height:45px;background:var(--red)}
  .nav-home{position:absolute;left:500px;top:62px;width:78px;height:45px;background:var(--navy-deep);border-bottom-left-radius:30px}
  .nav-item{position:absolute;top:62px;height:45px;display:flex;align-items:center;transform:translateX(-50%);font-family:"Exo 2",sans-serif;font-weight:700;font-size:14px;color:var(--white)}

  /* hero */
  .hero-title{left:0;width:1200px;top:412px;text-align:center;font-size:56px;line-height:1}
  .hero-tag{left:0;width:1200px;top:475px;text-align:center;font-family:"Oswald",sans-serif;font-size:33px;color:var(--ink)}
  .play{left:1092px;top:586px;width:42px;height:42px;border-radius:50%;background:var(--white);display:flex;align-items:center;justify-content:center}

  /* about */
  .about-text{left:597px;top:779px;width:451px;font-size:14px;line-height:24.8px;color:var(--muted);text-align:justify}

  /* services */
  .service{position:absolute;width:250px;text-align:center;top:1478px}
  .service h3{font-family:"Exo 2",sans-serif;font-weight:700;font-size:19px;color:var(--navy);margin-bottom:10px;letter-spacing:.3px}
  .service p{font-size:14px;line-height:20.6px;color:var(--muted);padding:0 18px}
  .service.is-active h3,.service.is-active p{color:var(--white)}

  /* contact */
  .field-label{position:absolute;left:146px;font-size:12px;color:var(--white)}
  .field-line{position:absolute;left:146px;width:373px;height:1px;background:rgba(255,255,255,.8)}
  .submit{background:var(--navy-deep)}

  /* footer */
  .foot-call{left:436px;top:2972px;display:flex;align-items:center;gap:8px;font-family:"Exo 2",sans-serif;font-weight:700;font-size:19px;color:var(--navy)}
  .socials{left:754px;top:2973px;display:flex;gap:7px}
  .social{width:24px;height:24px;border-radius:50%;border:1.5px solid #8a93b8}
  .foot-nav{left:436px;top:3024px;width:619px;display:flex;justify-content:space-between;font-family:"Exo 2",sans-serif;font-weight:700;font-size:15px;color:var(--navy)}
  .foot-nav .sep{font-weight:400}
  .copy{left:436px;top:3067px;font-size:13px;color:#444}
</style>
</head>
<body>

<svg class="backdrop" viewBox="0 0 1200 3145" xmlns="http://www.w3.org/2000/svg">
  <defs>
    <radialGradient id="heroGlow" cx="45%" cy="30%" r="80%">
      <stop offset="0" stop-color="#8a6a42"/><stop offset=".5" stop-color="#4a3420"/><stop offset="1" stop-color="#1c130c"/>
    </radialGradient>
    <linearGradient id="flagSunset" x1="0" y1="0" x2="0" y2="1">
      <stop offset="0" stop-color="#1d2e6b"/><stop offset=".45" stop-color="#c9413a"/><stop offset=".75" stop-color="#f2a33a"/><stop offset="1" stop-color="#5a2a1c"/>
    </linearGradient>
    <radialGradient id="navyField" cx="50%" cy="40%" r="70%">
      <stop offset="0" stop-color="#16267a"/><stop offset="1" stop-color="#0a1657"/>
    </radialGradient>
    <linearGradient id="towers" x1="0" y1="0" x2="1" y2="1">
      <stop offset="0" stop-color="#1c4fa8"/><stop offset=".5" stop-color="#6f9fdc"/><stop offset="1" stop-color="#1a3f8c"/>
    </linearGradient>
    <linearGradient id="sky1" x1="0" y1="0" x2="0" y2="1"><stop offset="0" stop-color="#9cc0e4"/><stop offset="1" stop-color="#2e5a98"/></linearGradient>
    <linearGradient id="shake" x1="0" y1="0" x2="1" y2="1"><stop offset="0" stop-color="#0d2142"/><stop offset=".55" stop-color="#3b5a86"/><stop offset="1" stop-color="#081630"/></linearGradient>
    <linearGradient id="house" x1="0" y1="0" x2="0" y2="1"><stop offset="0" stop-color="#d8dde2"/><stop offset="1" stop-color="#8d9499"/></linearGradient>
    <linearGradient id="capitol" x1="0" y1="0" x2="1" y2="0"><stop offset="0" stop-color="#8fb0d6"/><stop offset="1" stop-color="#e6e2d8"/></linearGradient>
    <clipPath id="heroClip"><rect x="0" y="107" width="1200" height="600"/></clipPath>
  </defs>

  <!-- hero -->
  <rect x="0" y="107" width="1200" height="600" fill="url(#heroGlow)" role="img" aria-label="Night crowd waving American flags under fireworks"/>
  <g clip-path="url(#heroClip)">
    <circle cx="600" cy="548" r="243" fill="#fff" stroke="var(--red)" stroke-width="10"/>
    <circle cx="600" cy="548" r="218" fill="none" stroke="var(--navy)" stroke-width="5"/>
  </g>
  <path d="M0 686 Q600 560 1200 686 L1200 720 L0 720 Z" fill="#fff"/>
  <path d="M0 686 Q600 560 1200 686" fill="none" stroke="var(--navy)" stroke-width="5"/>

  <!-- about image -->
  <circle cx="355" cy="893" r="207" fill="#fff" stroke="var(--red)" stroke-width="6"/>
  <circle cx="355" cy="893" r="190" fill="none" stroke="var(--navy)" stroke-width="5"/>
  <circle cx="355" cy="893" r="173" fill="url(#flagSunset)" role="img" aria-label="American flag with silhouettes of saluting soldiers at sunset"/>

  <!-- services band -->
  <path d="M0 1290 Q600 980 1200 1290 L1200 1895 Q600 1600 0 1895 Z" fill="url(#navyField)"/>
  <path d="M0 1280 Q600 970 1200 1280" fill="none" stroke="#fff" stroke-width="6"/>
  <path d="M0 1290 Q600 980 1200 1290" fill="none" stroke="var(--red)" stroke-width="8"/>

  <circle cx="302" cy="1507" r="155" fill="#fff"/>
  <circle cx="302" cy="1507" r="142" fill="none" stroke="var(--red)" stroke-width="3"/>
  <circle cx="898" cy="1507" r="155" fill="#fff"/>
  <circle cx="898" cy="1507" r="142" fill="none" stroke="var(--red)" stroke-width="3"/>
  <circle cx="600" cy="1507" r="158" fill="var(--red)" stroke="var(--navy-deep)" stroke-width="8"/>

  <!-- service icons -->
  <g fill="none" stroke="var(--red)" stroke-width="2.5" stroke-linejoin="round">
    <rect x="278" y="1400" width="22" height="50"/><rect x="304" y="1414" width="26" height="36"/>
    <line x1="283" y1="1410" x2="295" y2="1410"/><line x1="283" y1="1422" x2="295" y2="1422"/><line x1="283" y1="1434" x2="295" y2="1434"/>
    <line x1="310" y1="1424" x2="324" y2="1424"/><line x1="310" y1="1436" x2="324" y2="1436"/>
    <line x1="270" y1="1452" x2="336" y2="1452"/>
  </g>
  <g fill="none" stroke="#fff" stroke-width="2.5" stroke-linejoin="round">
    <path d="M578 1418 a22 22 0 0 1 44 0 Z"/><line x1="573" y1="1420" x2="627" y2="1420"/>
    <circle cx="600" cy="1432" r="11"/><path d="M574 1458 q0 -16 26 -16 q26 0 26 16 Z"/>
  </g>
  <g fill="none" stroke="var(--red)" stroke-width="2.5" stroke-linejoin="round">
    <rect x="868" y="1400" width="44" height="50"/><line x1="868" y1="1420" x2="890" y2="1420"/><line x1="868" y1="1435" x2="900" y2="1435"/>
    <path d="M904 1452 L932 1410 L938 1414 L910 1456 Z"/>
  </g>
  <g fill="none" stroke-width="2">
    <circle cx="302" cy="1627" r="11" stroke="var(--red)"/><path d="M296 1627 h11 m-4 -4 l4 4 l-4 4" stroke="var(--red)"/>
    <circle cx="600" cy="1627" r="11" stroke="#fff"/><path d="M594 1627 h11 m-4 -4 l4 4 l-4 4" stroke="#fff"/>
    <circle cx="898" cy="1627" r="11" stroke="var(--red)"/><path d="M892 1627 h11 m-4 -4 l4 4 l-4 4" stroke="var(--red)"/>
  </g>

  <!-- contact area -->
  <rect x="0" y="2100" width="1200" height="850" fill="url(#towers)" role="img" aria-label="Glass skyscrapers seen from below against a blue sky"/>
  <path d="M0 2100 L625 2100 C 665 2320 660 2660 380 2920 L0 2920 Z" fill="var(--red-soft)" stroke="#fff" stroke-width="6"/>
  <path d="M0 2160 Q600 2454 1200 2173 L1200 2090 L0 2090 Z" fill="#fff"/>
  <path d="M0 2805 Q600 3045 1200 2785 L1200 3145 L0 3145 Z" fill="#fff"/>
  <path d="M0 2805 Q600 3045 1200 2785" fill="none" stroke="var(--red)" stroke-width="8"/>

  <!-- gallery tiles -->
  <rect x="148" y="1948" width="216" height="208" rx="30" fill="url(#sky1)" role="img" aria-label="Glass office towers viewed from street level"/>
  <rect x="377" y="1948" width="216" height="208" rx="30" fill="url(#shake)" role="img" aria-label="Business handshake with digital light effects"/>
  <rect x="606" y="1948" width="216" height="208" rx="30" fill="url(#house)" role="img" aria-label="Modern house rendering over architectural plans"/>
  <rect x="835" y="1948" width="216" height="208" rx="30" fill="url(#capitol)" role="img" aria-label="Government building dome with American flag"/>
  <circle cx="715" cy="2055" r="17" fill="var(--navy-deep)"/>
  <path d="M715 2047 v16 M707 2055 h16" stroke="#fff" stroke-width="3"/>
</svg>

<!-- header -->
<div class="logo-disc"><span class="brand-name">TOVANDEX4</span></div>
<div class="call">
  <span class="call-icon"><svg width="14" height="14" viewBox="0 0 24 24"><path fill="#fff" d="M6.6 10.8a15 15 0 0 0 6.6 6.6l2.2-2.2c.3-.3.7-.4 1-.2 1.1.4 2.3.6 3.6.6.6 0 1 .4 1 1V20c0 .6-.4 1-1 1A17 17 0 0 1 3 4c0-.6.4-1 1-1h3.5c.6 0 1 .4 1 1 0 1.3.2 2.5.6 3.6.1.3 0 .7-.2 1z"/></svg></span>
  CALL US : +1 555 014 2290
</div>
<div class="nav-bar"></div>
<div class="nav-home"></div>
<nav>
  <span class="nav-item" style="left:543px">HOME</span>
  <span class="nav-item" style="left:628px">ABOUT</span>
  <span class="nav-item" style="left:719px">SERVICES</span>
  <span class="nav-item" style="left:821px">PROJECTS</span>
  <span class="nav-item" style="left:921px">CAREERS</span>
  <span class="nav-item" style="left:1018px">CONTACT</span>
</nav>

<!-- hero -->
<h1 class="abs heading hero-title">TOVANDEX4</h1>
<p class="abs hero-tag">Whatever it takes</p>
<a class="btn" style="left:531px;top:530px">GET STARTED</a>
<div class="abs play"><svg width="16" height="18" viewBox="0 0 16 18"><path d="M2 1 L15 9 L2 17 Z" fill="#111"/></svg></div>

<!-- about -->
<h2 class="abs heading" style="left:597px;top:697px">ABOUT US</h2>
<div class="underline" style="left:597px;top:752px"></div>
<p class="abs about-text">Sed ut perspiciatis unde omnis iste natus error sit voluptatem accusantium doloremque laudantium, totam rem aperiam, eaque ipsa quae ab illo inventore veritatis et quasi architecto beatae vitae dicta sunt explicabo. Nemo enim ipsam voluptatem quia voluptas sit aspernatur aut odit aut fugit, sed quia consequuntur magni dolores eos qui ratione voluptatem sequi nesciunt. Neque porro quisquam est, qui dolorem ipsum quia dolor sit amet, consectetur, adipisci velit, sed quia non numquam eius modi tempora incidunt ut labore et dolore magnam aliquam quaerat voluptatem.</p>
<a class="btn" style="left:597px;top:1028px">READ MORE</a>

<!-- services -->
<h2 class="abs heading" style="left:0;width:1200px;text-align:center;top:1234px;color:var(--white)">OUR SERVICES</h2>
<div class="underline" style="left:589px;top:1290px"></div>
<div class="service" style="left:177px"><h3>ARCHITECTURE</h3><p>Sed ut perspiciatis unde omnis iste natus error sit voluptatem accusantium doloremque ntium, totam rem aperiam, eaque</p></div>
<div class="service is-active" style="left:475px"><h3>ENGINEER</h3><p>Sed ut perspiciatis unde omnis iste natus error sit voluptatem accusantium doloremque ntium, totam rem aperiam, eaque</p></div>
<div class="service" style="left:773px"><h3>DESIGN BUILD</h3><p>Sed ut perspiciatis unde omnis iste natus error sit voluptatem accusantium doloremque ntium, totam rem aperiam, eaque</p></div>

<!-- gallery -->
<h2 class="abs heading" style="left:0;width:1200px;text-align:center;top:1840px">PROJECT GALLERY</h2>
<div class="underline" style="left:589px;top:1896px"></div>
<a class="btn" style="left:531px;top:2196px">LOAD MORE</a>

<!-- contact -->
<h2 class="abs heading" style="left:146px;top:2337px;color:var(--white)">CONTACT</h2>
<div class="underline" style="left:146px;top:2393px;background:var(--white)"></div>
<label class="field-label" style="top:2440px">Enter Name</label><div class="field-line" style="top:2473px"></div>
<label class="field-label" style="top:2496px">Enter Email</label><div class="field-line" style="top:2529px"></div>
<label class="field-label" style="top:2553px">Enter Phone</label><div class="field-line" style="top:2586px"></div>
<label class="field-label" style="top:2610px">Message</label><div class="field-line" style="top:2707px"></div>
<a class="btn submit" style="left:146px;top:2740px">SUBMIT</a>

<!-- footer -->
<div class="abs" style="left:145px;top:3010px;display:flex;align-items:center;gap:10px">
  <span style="width:22px;height:22px;border-radius:50%;background:var(--red)"></span>
  <span class="brand-name" style="font-size:40px">TOVANDEX4</span>
</div>
<div class="abs foot-call">
  <span class="call-icon"><svg width="14" height="14" viewBox="0 0 24 24"><path fill="#fff" d="M6.6 10.8a15 15 0 0 0 6.6 6.6l2.2-2.2c.3-.3.7-.4 1-.2 1.1.4 2.3.6 3.6.6.6 0 1 .4 1 1V20c0 .6-.4 1-1 1A17 17 0 0 1 3 4c0-.6.4-1 1-1h3.5c.6 0 1 .4 1 1 0 1.3.2 2.5.6 3.6.1.3 0 .7-.2 1z"/></svg></span>
  CALL US : +1 555 014 2290
</div>
<div class="abs socials"><span class="social"></span><span class="social"></span><span class="social"></span><span class="social"></span><span class="social"></span></div>
<div class="abs foot-nav">
  <span>HOME</span><span class="sep">/</span><span>ABOUT</span><span class="sep">/</span><span>SERVICES</span><span class="sep">/</span><span>PROJECTS</span><span class="sep">/</span><span>CAREERS</span><span class="sep">/</span><span>CONTACT</span>
</div>
<p class="abs copy">©2024 Tovandex4. All rights reserved &nbsp;|&nbsp; Privacy &nbsp;|&nbsp; Terms of Use</p>

</body>
</html>
```